Harbor Crestline (Business Card Design)

Need business cards designed. Something modern, chic, and sleek. Mabye the back of the card should be the navy blue that is in the logo and then just the logo on the back.

Target Market(s)

Those in the hotel, office, and renovation industry

Contact Information for Business Card

1. Logo 2. Dorian Fenwick 3. CEO/Founder 4. Phone: (833) HarbCre / (833) 427-2731 5. Email: dorian@theharborcrestline.com 6. Website: www.theharborcrestline.com

Font styles to use
Other font styles liked:
• Look at the logo font and base the font for everything else off of that.

Colors
0054AA
0677BA
7BADD7
CADEEF
E8F1F8

Requirements
Must have
• Colors that are associated in the logo
Nice to have
• Sleek modern clean and chic design.

```html
<!DOCTYPE html>
<html lang="en">
<head>
<meta charset="UTF-8">
<title>Harbor Crestline — Business Cards</title>
<link href="https://fonts.googleapis.com/css2?family=Montserrat:wght@400;500;600;700&display=swap" rel="stylesheet">
<style>
  :root {
    --navy: #101a45;
    --gold: #cfa648;
    --paper: #ffffff;
    --backdrop: #e4e5e8;
    --ink-grey: #555a66;
    --rule-grey: #c4c6cc;
  }
  * { box-sizing: border-box; margin: 0; padding: 0; }
  html, body {
    width: 1200px; height: 800px; overflow: hidden;
    background: var(--backdrop);
    font-family: "Montserrat", sans-serif;
  }
  .sheet {
    width: 1200px; height: 800px;
    display: flex; align-items: center; justify-content: center; gap: 40px;
  }
  .card {
    position: relative;
    width: 540px; height: 308px;
    overflow: hidden;
    box-shadow: 0 10px 24px rgba(20, 26, 50, 0.18);
  }

  /* Front */
  .card--front { background: var(--paper); }
  .holder { position: absolute; left: 40px; top: 44px; white-space: nowrap; }
  .holder__name {
    font-weight: 700; font-size: 18px; letter-spacing: 0.4px;
    color: var(--navy); text-transform: uppercase;
  }
  .holder__title { font-size: 13px; color: var(--ink-grey); margin-top: 3px; }
  .holder__rule {
    position: absolute; left: 250px; top: 92px;
    width: 256px; height: 1px; background: var(--rule-grey);
  }
  .contact { position: absolute; left: 40px; top: 110px; list-style: none; }
  .contact__item {
    display: flex; align-items: center; gap: 9px;
    font-size: 12.5px; color: var(--ink-grey); line-height: 23px;
    white-space: nowrap;
  }
  .contact__item svg { width: 12px; height: 12px; flex: none; }
  .contact__accent { color: var(--gold); }
  .brand {
    position: absolute; right: 34px; top: 50px;
    display: flex; align-items: center; gap: 9px;
    white-space: nowrap;
  }
  .brand__square { width: 16px; height: 16px; background: var(--navy); flex: none; }
  .brand__name {
    font-weight: 600; font-size: 19px; letter-spacing: 1.5px;
    color: var(--navy); text-transform: uppercase;
  }
  .front-band {
    position: absolute; left: 0; bottom: 0; width: 100%; height: 44px;
    background: var(--navy);
  }
  .front-band__square {
    position: absolute; right: 30px; top: 14px;
    width: 16px; height: 16px; border: 2px solid var(--paper);
  }

  /* Back */
  .card--back { background: var(--navy); }
  .back-band {
    position: absolute; left: 0; bottom: 0; width: 100%; height: 48px;
    background: var(--gold);
  }
  .back-band__square {
    position: absolute; left: 26px; top: 15px;
    width: 18px; height: 18px; background: var(--navy);
  }
  .back-brand {
    position: absolute; right: 40px; top: 150px;
    display: flex; align-items: center; gap: 12px;
    white-space: nowrap;
  }
  .back-brand__square { width: 22px; height: 22px; border: 3px solid var(--paper); flex: none; }
  .back-brand__name {
    font-weight: 600; font-size: 24px; letter-spacing: 2.5px;
    color: var(--paper); text-transform: uppercase;
  }
</style>
</head>
<body>
<main class="sheet">
  <section class="card card--front" aria-label="Business card front">
    <div class="holder">
      <p class="holder__name">Dorian Fenwick</p>
      <p class="holder__title">CEO/Founder</p>
    </div>
    <div class="holder__rule"></div>
    <ul class="contact">
      <li class="contact__item">
        <svg viewBox="0 0 12 12" aria-hidden="true"><path fill="#cfa648" d="M2.3 1h2l1 2.6-1.3 1a6 6 0 0 0 3.4 3.4l1-1.3L11 7.7v2A1.3 1.3 0 0 1 9.7 11 8.7 8.7 0 0 1 1 2.3 1.3 1.3 0 0 1 2.3 1z"/></svg>
        <span>(833) HarbCre <span class="contact__accent">/</span> (833) 427-2731</span>
      </li>
      <li class="contact__item">
        <svg viewBox="0 0 12 12" aria-hidden="true"><rect x="0.5" y="2" width="11" height="8" rx="1" fill="#cfa648"/><path d="M1 3l5 3.6L11 3" fill="none" stroke="#fff" stroke-width="1.1"/></svg>
        <span>dorian@<span class="contact__accent">theharborcrestline</span>.com</span>
      </li>
      <li class="contact__item">
        <svg viewBox="0 0 12 12" aria-hidden="true"><circle cx="6" cy="6" r="5" fill="none" stroke="#cfa648" stroke-width="1.3"/><path d="M1 6h10M6 1c-2.6 2.8-2.6 7.2 0 10M6 1c2.6 2.8 2.6 7.2 0 10" fill="none" stroke="#cfa648" stroke-width="1"/></svg>
        <span>www.<span class="contact__accent">theharborcrestline</span>.com</span>
      </li>
    </ul>
    <div class="brand">
      <span class="brand__square"></span>
      <span class="brand__name">Harbor Crestline</span>
    </div>
    <div class="front-band"><span class="front-band__square"></span></div>
  </section>

  <section class="card card--back" aria-label="Business card back">
    <div class="back-brand">
      <span class="back-brand__square"></span>
      <span class="back-brand__name">Harbor Crestline</span>
    </div>
    <div class="back-band"><span class="back-band__square"></span></div>
  </section>
</main>
</body>
</html>
```